A slider bar and icons to be used on the map

#Background
We are currently creating a website for tourists to Japan . Named "Torii Path," It's a website where users can search for shrines and temples across Japan on the map. We are seeking designs for three icons(shrine icon, temple icon, and representing both shrine and temple icon) and a slider bar to be used on this site's map.
#Requirements
Cool and understandable icons and a slider bar that match the web design.
#Web Design Concept
Attached is a reference document.
#Desired Items
We need four items written below.
-Shrine icon
-Temple icon
-Icon representing both shrines and temples (expressed as a single icon)
-Slider bar
#Regarding the Slider Bar
It has two functions:
-Filter popular shrines and temples.
-Filiter shrines and temples with cool kanji.
We would like it to be able to filter from both the right and the left.
We want to express that moving to the right represents popularity or cool kanji. We'd like to express this on the slider bar as a design.
* reference> https://pics.example-lens.net/k7PqWx2mZ9vTbR4aN
Target Market(s)
Inbound tourists to Japan
Look and feel
Each slider illustrates characteristics of the customer's brand and the style your logo design should communicate.

```html
<!DOCTYPE html>
<html lang="en">
<head>
<meta charset="utf-8">
<title>Torii Path – Map Filter Sliders</title>
<link href="https://fonts.googleapis.com/css2?family=Poppins:wght@400;500&display=swap" rel="stylesheet">
<style>
  :root {
    --bg: #ffffff;
    --panel-border: #bdbdbd;
    --select-border: #a9a9a9;
    --text-strong: #222222;
    --text-label: #444444;
    --caret: #6b6b6b;
    --histogram: #dfe9f8;
    --track: #e4e4e4;
    --track-edge: #d4d4d4;
    --tier-outer: #f4b731;
    --tier-mid: #f58634;
    --tier-core: #e62226;
    --handle-fill: #ffffff;
    --handle-edge: #a8a8a8;
  }
  * { box-sizing: border-box; margin: 0; padding: 0; }
  html, body {
    width: 1200px; height: 1177px; overflow: hidden;
    background: var(--bg);
    font-family: "Poppins", sans-serif;
  }
  .filter-stack { position: relative; width: 1200px; height: 1177px; }
  .filter-panel {
    position: absolute; left: 188.5px;
    width: 823px; height: 125px;
    border: 1.5px solid var(--panel-border);
    border-radius: 2px;
  }
  .filter-panel svg.slider-art {
    position: absolute; inset: 0; width: 100%; height: 100%;
  }
  .mode-select {
    position: absolute; left: 15px; top: 61px;
    width: 162px; height: 45px;
    border: 1.5px solid var(--select-border);
    border-radius: 5px;
    display: flex; align-items: center;
    padding-left: 13px;
    font-size: 18.5px; font-weight: 500; color: var(--text-strong);
  }
  .mode-select .caret {
    position: absolute; right: 13px; top: 16px;
    width: 13px; height: 11px;
  }
  .scale-label {
    position: absolute; top: 40px;
    font-size: 16px; color: var(--text-label); line-height: 1;
  }
  .scale-label.low { left: 206px; }
  .scale-label.high { right: 26px; }
  .bar { fill: var(--histogram); }
  .track { fill: var(--track); stroke: var(--track-edge); stroke-width: 1.5; }
  .tier-outer { fill: var(--tier-outer); }
  .tier-mid { fill: var(--tier-mid); }
  .tier-core { fill: var(--tier-core); }
  .handle { fill: var(--handle-fill); stroke: var(--handle-edge); stroke-width: 1.5; stroke-linejoin: round; }
</style>
</head>
<body>
<svg width="0" height="0" style="position:absolute">
  <defs>
    <g id="histogram">
      <rect class="bar" x="531" y="103" width="17" height="24" rx="8.5"/>
      <rect class="bar" x="561" y="93" width="17" height="34" rx="8.5"/>
      <rect class="bar" x="591" y="83" width="17" height="44" rx="8.5"/>
      <rect class="bar" x="621" y="73" width="17" height="54" rx="8.5"/>
      <rect class="bar" x="652" y="63" width="17" height="64" rx="8.5"/>
      <rect class="bar" x="682" y="53" width="17" height="74" rx="8.5"/>
      <rect class="bar" x="712" y="43" width="17" height="84" rx="8.5"/>
      <rect class="bar" x="742" y="33" width="17" height="94" rx="8.5"/>
      <rect class="bar" x="772" y="23" width="17" height="104" rx="8.5"/>
      <rect class="bar" x="803" y="13" width="17" height="114" rx="8.5"/>
      <rect class="bar" x="833" y="23" width="17" height="104" rx="8.5"/>
      <rect class="bar" x="863" y="33" width="17" height="94" rx="8.5"/>
      <rect class="bar" x="893" y="43" width="17" height="84" rx="8.5"/>
      <rect class="bar" x="923" y="53" width="17" height="74" rx="8.5"/>
      <rect class="bar" x="954" y="63" width="17" height="64" rx="8.5"/>
      <rect class="bar" x="984" y="73" width="17" height="54" rx="8.5"/>
      <rect class="bar" x="1014" y="83" width="17" height="44" rx="8.5"/>
      <rect class="bar" x="1044" y="93" width="17" height="34" rx="8.5"/>
      <rect class="bar" x="1074" y="103" width="17" height="24" rx="8.5"/>
      <rect class="track" x="338" y="127" width="948" height="22" rx="11"/>
    </g>
    <path id="handle" class="handle" d="M0 14 L17 0 L34 14 L34 48 L0 48 Z"/>
    <g id="range-narrow">
      <rect class="tier-core" x="717" y="127" width="189" height="22"/>
      <use href="#handle" x="683" y="106"/>
      <use href="#handle" x="906" y="106"/>
    </g>
    <g id="range-medium">
      <rect class="tier-mid" x="543" y="127" width="174" height="22"/>
      <rect class="tier-core" x="717" y="127" width="189" height="22"/>
      <rect class="tier-mid" x="906" y="127" width="170" height="22"/>
      <use href="#handle" x="509" y="106"/>
      <use href="#handle" x="1076" y="106"/>
    </g>
    <g id="range-full">
      <rect class="tier-outer" x="371" y="127" width="157" height="22"/>
      <rect class="tier-mid" x="528" y="127" width="189" height="22"/>
      <rect class="tier-core" x="717" y="127" width="189" height="22"/>
      <rect class="tier-mid" x="906" y="127" width="189" height="22"/>
      <rect class="tier-outer" x="1095" y="127" width="158" height="22"/>
      <use href="#handle" x="338" y="106"/>
      <use href="#handle" x="1253" y="106"/>
    </g>
    <path id="caret-shape" d="M0 0 H13 L6.5 11 Z" fill="#6b6b6b"/>
  </defs>
</svg>

<main class="filter-stack">
  <section class="filter-panel" style="top:122px">
    <svg class="slider-art" viewBox="0 0 1331 202" preserveAspectRatio="none"><use href="#histogram"/><use href="#range-narrow"/></svg>
    <div class="mode-select">Popular<svg class="caret" viewBox="0 0 13 11"><use href="#caret-shape"/></svg></div>
    <span class="scale-label low">Hidden</span><span class="scale-label high">Popular</span>
  </section>

  <section class="filter-panel" style="top:283px">
    <svg class="slider-art" viewBox="0 0 1331 202" preserveAspectRatio="none"><use href="#histogram"/><use href="#range-medium"/></svg>
    <div class="mode-select">Popular<svg class="caret" viewBox="0 0 13 11"><use href="#caret-shape"/></svg></div>
    <span class="scale-label low">Hidden</span><span class="scale-label high">Popular</span>
  </section>

  <section class="filter-panel" style="top:446px">
    <svg class="slider-art" viewBox="0 0 1331 202" preserveAspectRatio="none"><use href="#histogram"/><use href="#range-full"/></svg>
    <div class="mode-select">Popular<svg class="caret" viewBox="0 0 13 11"><use href="#caret-shape"/></svg></div>
    <span class="scale-label low">Hidden</span><span class="scale-label high">Popular</span>
  </section>

  <section class="filter-panel" style="top:609px">
    <svg class="slider-art" viewBox="0 0 1331 202" preserveAspectRatio="none"><use href="#histogram"/><use href="#range-narrow"/></svg>
    <div class="mode-select">Stylish Kanji<svg class="caret" viewBox="0 0 13 11"><use href="#caret-shape"/></svg></div>
    <span class="scale-label low">Simple</span><span class="scale-label high">Stylish</span>
  </section>

  <section class="filter-panel" style="top:771px">
    <svg class="slider-art" viewBox="0 0 1331 202" preserveAspectRatio="none"><use href="#histogram"/><use href="#range-medium"/></svg>
    <div class="mode-select">Stylish Kanji<svg class="caret" viewBox="0 0 13 11"><use href="#caret-shape"/></svg></div>
    <span class="scale-label low">Simple</span><span class="scale-label high">Stylish</span>
  </section>

  <section class="filter-panel" style="top:933px">
    <svg class="slider-art" viewBox="0 0 1331 202" preserveAspectRatio="none"><use href="#histogram"/><use href="#range-full"/></svg>
    <div class="mode-select">Stylish Kanji<svg class="caret" viewBox="0 0 13 11"><use href="#caret-shape"/></svg></div>
    <span class="scale-label low">Simple</span><span class="scale-label high">Stylish</span>
  </section>
</main>
</body>
</html>
```